Its time for a new website

We are at a point now where we are in desperate need of a new website. It was last updated 2006 but still looks like its 1995. We are looking for something eye catching to our clients but easy to navigate and add/remove photos of jobs/trucks and information. Our key business is the manufacture of fire appliances and resale of parts and equipment.

www.kestrelrigs.com.au

Coding

Coded - Design and coding required

Number of Pages Required

5+ page

Requirements
Must have
• Logo

```html
<!DOCTYPE html>
<html lang="en">
<head>
<meta charset="utf-8">
<title>Kestrel Fire Rigs</title>
<link href="https://fonts.googleapis.com/css2?family=Open+Sans:wght@400;600;700&family=Comfortaa:wght@700&display=swap" rel="stylesheet">
<style>
:root{
  --header-bg:#241a17;
  --fire-red:#d21f1a;
  --brand-blue:#1a7fc1;
  --text-gray:#7a7a7a;
  --heading-gray:#555;
  --panel-gray:#ececec;
  --white:#fff;
  --footer-bg:#2b2b2b;
}
*{margin:0;padding:0;box-sizing:border-box}
html,body{width:845px;height:1200px;overflow:hidden;background:#fff;font-family:'Open Sans',sans-serif}
.page{position:relative;width:845px;height:1200px}
.site-header{position:absolute;top:0;left:0;width:845px;height:88px;background:var(--header-bg);border-top:2px solid var(--fire-red)}
.site-header::after{content:"";position:absolute;left:0;right:0;bottom:-4px;height:4px;background:var(--fire-red)}
.brand{position:absolute;left:70px;top:22px;display:flex;align-items:center;gap:8px}
.brand-dot{width:26px;height:26px;border-radius:50%;background:var(--fire-red)}
.brand-name{font-size:13px;font-weight:600;color:var(--brand-blue)}
.header-phone{position:absolute;right:69px;top:19px;font-size:8.5px;color:var(--white)}
.main-nav{position:absolute;right:69px;top:52px;display:flex;gap:21px;font-size:7px;font-weight:600;color:var(--white);text-transform:uppercase}
.main-nav .active{color:var(--brand-blue)}
.hero{position:absolute;top:92px;left:0;width:845px;height:306px;background:linear-gradient(100deg,#2a1a16 0%,#3a1a12 30%,#8a2410 55%,#d04a18 75%,#3a1410 100%)}
.hero-title{position:absolute;top:110px;left:0;width:845px;text-align:center;font-size:23.5px;line-height:37px;color:var(--white);text-shadow:0 1px 3px rgba(0,0,0,.5)}
.hero-dots{position:absolute;top:247px;left:418px;display:flex;gap:4px}
.hero-dots span{width:8px;height:8px;border-radius:50%;background:var(--white)}
.hero-dots span:first-child{background:var(--fire-red)}
.intro{position:absolute;top:398px;left:0;width:845px;height:138px;text-align:center}
.intro h1{margin-top:23px;font-size:15px;font-weight:700;color:var(--fire-red)}
.intro h2{margin-top:10px;font-size:11.5px;font-weight:600;color:var(--brand-blue)}
.intro p{margin-top:6px;font-size:8px;line-height:19px;color:var(--text-gray)}
.work{position:absolute;top:536px;left:0;width:845px;height:302px;background:var(--panel-gray)}
.work h2{position:absolute;top:20px;width:100%;text-align:center;font-size:14px;font-weight:700;color:var(--heading-gray)}
.work .lead{position:absolute;top:54px;width:100%;text-align:center;font-size:8px;color:var(--heading-gray)}
.card{position:absolute;top:100px;width:166px}
.card-img{width:166px;height:114px}
.card h3{margin-top:12px;font-size:10px;font-weight:400;color:var(--fire-red)}
.card p{margin-top:4px;font-size:7.2px;line-height:17px;color:var(--text-gray)}
.map{position:absolute;top:838px;left:0;width:845px;height:294px;background:linear-gradient(135deg,#dedad2,#e8e4dc 50%,#d8d4cc)}
.contact-panel{position:absolute;top:869px;left:70px;width:571px;height:236px;background:rgba(90,90,90,.82)}
.contact-panel h2{position:absolute;top:16px;left:0;width:275px;text-align:center;font-size:12px;font-weight:700;color:var(--white)}
.field{position:absolute;background:var(--white);border:1px solid #ccc;font-size:7.5px;font-style:italic;color:#999;padding:7px}
.submit{position:absolute;left:232px;top:202px;width:69px;height:24px;background:var(--brand-blue);color:var(--white);font-size:7.5px;font-weight:700;letter-spacing:.6px;display:flex;align-items:center;justify-content:center}
.contact-info{position:absolute;left:336px;top:62px;font-size:8.3px;line-height:15px;color:var(--white)}
.contact-info li{list-style:none;display:flex;gap:8px;margin-bottom:8px}
.contact-info svg{flex:none;margin-top:3px}
.site-footer{position:absolute;top:1132px;left:0;width:845px;height:68px;background:var(--footer-bg)}
.footer-nav{position:absolute;left:70px;top:17px;font-size:7px;color:var(--white)}
.copyright{position:absolute;left:70px;top:44px;font-size:6.5px;color:#888}
.copyright b{color:var(--white);font-weight:400}
.social{position:absolute;left:645px;top:22px;display:flex;gap:5px}
.social span{width:22px;height:22px;border-radius:50%}
</style>
</head>
<body>
<div class="page">
  <header class="site-header">
    <div class="brand"><span class="brand-dot"></span><span class="brand-name">Kestrel Fire Rigs</span></div>
    <div class="header-phone">Phone - 08 9555 0142 &nbsp;- &nbsp;Phone (International) +61 8 9555 0142</div>
    <nav class="main-nav">
      <span class="active">Home</span><span>About us</span><span>Pumpers</span><span>Tankers</span><span>GPA/Resue</span><span>Light tankers</span><span>Trailers</span><span>Slip-on units</span><span>Contact us</span>
    </nav>
  </header>

  <section class="hero" role="img" aria-label="Hands holding a red fire extinguisher in front of flames">
    <div class="hero-title">Kestrel Fire Rigs are Western Australia's<br>leading manufacturer</div>
    <div class="hero-dots"><span></span><span></span><span></span></div>
  </section>

  <section class="intro">
    <h1>KESTREL FIRE RIGS !</h1>
    <h2>Kestrel Fire Rigs are Western Australia's leading manufacturer of custom firefighting equipment</h2>
    <p>Fire-Brigade Captain and 35-year veteran volunteer Fire-fighter, Graham Ellery, established Kestrel Fire Rigs in 1988. As a fully Qualified automotive motor<br>an ever increasing range of high Quality, Functional and Affordable fire appliances suited to the harsh Australian environment.!</p>
  </section>

  <section class="work">
    <h2>ABOUT OUR WORK</h2>
    <p class="lead">Es simplemente el texto de relleno de las imprentas y archivos de texto. Lorem Ipsum ha sido el texto de relleno estándar de las...</p>
    <div class="card" style="left:70px"><div class="card-img" role="img" aria-label="Red pumper fire truck" style="background:linear-gradient(180deg,#a9b4bf,#b83226 55%,#8a8478)"></div><h3>Pumpers</h3><p>Es simplemente el texto de relleno de las imprentas y archivos de texto.</p></div>
    <div class="card" style="left:250px"><div class="card-img" role="img" aria-label="White tanker truck" style="background:linear-gradient(180deg,#7f8a94,#dcdcd6 55%,#6e6a62)"></div><h3>Tankers</h3><p>Es simplemente el texto de relleno de las imprentas y archivos de texto.</p></div>
    <div class="card" style="left:430px"><div class="card-img" role="img" aria-label="General purpose fire appliance" style="background:linear-gradient(180deg,#5a5a58,#c43a30 50%,#9a9690)"></div><h3>General Purpose</h3><p>Es simplemente el texto de relleno de las imprentas y archivos de texto.</p></div>
    <div class="card" style="left:610px"><div class="card-img" role="img" aria-label="White light tanker with red stripes" style="background:linear-gradient(180deg,#8a9a7a,#eeeeea 50%,#b8a88e)"></div><h3>Light Tankers</h3><p>Es simplemente el texto de relleno de las imprentas y archivos de texto.</p></div>
  </section>

  <section class="map" role="img" aria-label="Street map showing the workshop location"></section>
  <div class="contact-panel">
    <h2>CONTACTS</h2>
    <div class="field" style="left:25px;top:54px;width:132px;height:28px">Your name</div>
    <div class="field" style="left:170px;top:54px;width:132px;height:28px">Your email</div>
    <div class="field" style="left:25px;top:96px;width:277px;height:92px">Your message</div>
    <div class="submit">SUBMIT</div>
    <ul class="contact-info">
      <li><svg width="7" height="9" viewBox="0 0 7 9"><path d="M3.5 0a3.5 3.5 0 0 0-3.5 3.5C0 6 3.5 9 3.5 9S7 6 7 3.5A3.5 3.5 0 0 0 3.5 0z" fill="#fff"/><circle cx="3.5" cy="3.5" r="1.2" fill="#5a5a5a"/></svg><span>Lot 14 Tuart Road Corrigin 6375 Western<br>Australia</span></li>
      <li><svg width="8" height="8" viewBox="0 0 8 8"><rect x=".5" y=".5" width="7" height="7" rx="1.5" fill="none" stroke="#fff"/><path d="M2 2h1.3l.5 1.3-.7.6c.3.6.6.9 1.1 1.1l.6-.7L6 4.8V6c-2.2 0-4-1.8-4-4z" fill="#fff"/></svg><span>08 9555 0142 &nbsp;&nbsp;fax (Aust) &nbsp;- 08 9555 0143</span></li>
      <li><svg width="9" height="7" viewBox="0 0 9 7"><rect x=".5" y=".5" width="8" height="6" fill="none" stroke="#fff"/><path d="M.5.5l4 3 4-3" fill="none" stroke="#fff"/></svg><span>info@kestrelrigs.com.au</span></li>
    </ul>
  </div>

  <footer class="site-footer">
    <div class="footer-nav">HOME &nbsp;/ &nbsp;ABOUT US &nbsp;/ &nbsp;PUMPERS &nbsp;/ &nbsp;TANKERS &nbsp;/ &nbsp;GPA/RESUE &nbsp;/ &nbsp;LIGHT TANKERS &nbsp;/ &nbsp;TRAILERS &nbsp;/ &nbsp;SLIP-ON UNITS &nbsp;/ &nbsp;CONTACT US</div>
    <div class="copyright">@ 2015. <b>KESTREL</b>. ALL RIGHTS RESERVED.</div>
    <div class="social"><span style="background:#3b66b0"></span><span style="background:#3fa6e0"></span><span style="background:#1d8fc9"></span><span style="background:#f2a11f"></span><span style="background:#d62b22"></span></div>
  </footer>
</div>
</body>
</html>
```